Animal Eye Clinic needs a Business card

We are a new veterinary ophthalmology practice (Ridgeline Pet Vision Care) and we need a business card designed. We only see animal eyes - we are not a regular veterinary clinic. We already have a logo. We are looking for a professional, good looking business card to hand out to our clients. We are looking for something simple but professional and contemporary. Our logo is likely the only picture/graphic that needs to be on the card.
Updates

Contact Information for Business Card

Delia Vossman, BSc, DVM, MSc, DipACVO
Veterinary Ophthalmologist

Phone: 250.418.3927
Email: ridgelinepetvisioncare@mailbox-example.net
Website: ridgelinepetvisioncare-example.net
Address: 1874 Thornbury Rd
Kelowna, BC, V1X 4M9

Colors

Designer to choose colors to be used in the design.

Requirements
Must have
• Our logo (attached)

```html
<!DOCTYPE html>
<html lang="en">
<head>
<meta charset="utf-8">
<title>Ridgeline Pet Vision Care – Business Card</title>
<link rel="stylesheet" href="https://fonts.googleapis.com/css2?family=Archivo:wght@400;700;800&family=Roboto+Condensed:wght@400;700&display=swap">
<style>
  :root {
    --teal: #1b9aaa;
    --teal-deep: #178d9c;
    --ink-grey: #5f6366;
    --paper: #ffffff;
    --stage: #222324;
  }
  * { box-sizing: border-box; margin: 0; padding: 0; }
  html, body { width: 1200px; height: 900px; overflow: hidden; }
  body {
    background: var(--stage);
    position: relative;
    font-family: "Roboto Condensed", "Arial Narrow", sans-serif;
  }
  .card {
    position: absolute;
    left: 250px;
    width: 700px;
    height: 400px;
    overflow: hidden;
  }
  /* back side */
  .card-back {
    top: 35px;
    background: var(--teal);
    display: flex;
    align-items: center;
    justify-content: center;
  }
  .brand-mark {
    display: flex;
    align-items: center;
    gap: 14px;
    font-family: "Archivo", Arial, sans-serif;
    font-weight: 700;
    font-size: 26px;
    color: var(--paper);
    letter-spacing: 0.5px;
  }
  .brand-dot {
    width: 22px; height: 22px;
    border-radius: 50%;
    background: var(--paper);
  }
  /* front side */
  .card-front {
    top: 465px;
    background: var(--paper);
  }
  .front-disc {
    position: absolute;
    left: 430px;
    top: -40px;
    width: 480px;
    height: 480px;
    border-radius: 50%;
    background: var(--teal);
  }
  .front-brand {
    position: absolute;
    left: 470px;
    top: 180px;
    width: 210px;
    font-family: "Archivo", Arial, sans-serif;
    font-weight: 700;
    font-size: 22px;
    line-height: 1.25;
    color: var(--paper);
    text-align: center;
  }
  .details {
    position: absolute;
    left: 40px;
    top: 32px;
  }
  .practice-name {
    font-family: "Archivo", Arial, sans-serif;
    font-weight: 700;
    font-size: 28px;
    line-height: 1.05;
    color: var(--teal);
    text-transform: uppercase;
    width: 400px;
  }
  .person-name {
    margin-top: 18px;
    font-family: "Archivo", Arial, sans-serif;
    font-weight: 800;
    font-size: 30px;
    color: var(--teal);
    text-transform: uppercase;
    letter-spacing: 0.5px;
  }
  .credentials {
    font-weight: 700;
    font-size: 17px;
    color: var(--teal);
  }
  .role {
    font-size: 18px;
    color: var(--ink-grey);
  }
  .address {
    margin-top: 14px;
    font-size: 18px;
    line-height: 1.3;
    color: var(--ink-grey);
  }
  .contact-list {
    list-style: none;
    margin-top: 14px;
  }
  .contact-list li {
    display: flex;
    align-items: center;
    gap: 10px;
    font-size: 17px;
    color: var(--ink-grey);
    line-height: 1.55;
  }
  .contact-list svg { width: 20px; height: 20px; flex: none; }
</style>
</head>
<body>

<section class="card card-back" aria-label="Business card back">
  <div class="brand-mark"><span class="brand-dot"></span>Ridgeline Pet Vision Care</div>
</section>

<section class="card card-front" aria-label="Business card front">
  <div class="front-disc"></div>
  <div class="front-brand">Ridgeline Pet Vision Care</div>

  <div class="details">
    <h1 class="practice-name">Ridgeline<br>Pet Vision Care</h1>
    <h2 class="person-name">Delia Vossman</h2>
    <p class="credentials">BSc, DVM, MSc, DipACVO</p>
    <p class="role">Veterinary Ophthalmologist</p>
    <p class="address">1874 Thornbury Rd<br>Kelowna, BC, V1X 4M9</p>
    <ul class="contact-list">
      <li>
        <svg viewBox="0 0 24 24" fill="none" stroke="var(--teal)" stroke-width="2" stroke-linecap="round" stroke-linejoin="round"><path d="M22 16.9v3a2 2 0 0 1-2.2 2 19.8 19.8 0 0 1-8.6-3.1 19.5 19.5 0 0 1-6-6A19.8 19.8 0 0 1 2.1 4.2 2 2 0 0 1 4.1 2h3a2 2 0 0 1 2 1.7c.1.9.4 1.8.7 2.7a2 2 0 0 1-.5 2.1L8 9.8a16 16 0 0 0 6 6l1.3-1.3a2 2 0 0 1 2.1-.4c.9.3 1.8.6 2.7.7a2 2 0 0 1 1.7 2z"/></svg>
        250.418.3927
      </li>
      <li>
        <svg viewBox="0 0 24 24" fill="none" stroke="var(--teal)" stroke-width="2" stroke-linejoin="round"><rect x="2" y="5" width="20" height="14" rx="1"/><path d="M2 6l10 7 10-7"/></svg>
        ridgelinepetvisioncare@mailbox-example.net
      </li>
      <li>
        <svg viewBox="0 0 24 24" fill="none" stroke="var(--teal)" stroke-width="2"><circle cx="12" cy="12" r="10"/><path d="M2 12h20M12 2c3 3 3 17 0 20M12 2c-3 3-3 17 0 20"/></svg>
        www.ridgelinepetvisioncare-example.net
      </li>
    </ul>
  </div>
</section>

</body>
</html>
```